BrivoTerna. Lantern of the Steady Harvest. Business card

Professional business card for BrivoTerna (Lantern of the Steady Harvest)
My rationale: Strategy-> Execution-> Results-> Value that lead to the BrivoTerna name: We put the Lantern of the Steady Harvest.
We deliver value to our customers helping them at defining a good strategy (cyan arrow). 90% of well formulated strategies fail due to poor execution so we also consider strategical execution very important (green arrow). Due to the execution we obtain the results (blue arrow). Finally, the results provide feedback to redefine strategy, and the new strategy has to be executed and new results obtained providing new feedback and on and on. It's like a wheel that finally, must create corporate value: value for shareholders, staholders, employees, providers...-

Target Market(s)

CEOs and steering comitees , invewrnent funds

Industry/Entity Type

Business Consultant

Contact Information for Business Card

Teodoro Vinsquel
CEO & Founder
teodoro.vinsquel@brivoterna-example.com
Mobile: +34 655.803.912
www.brivoterna-example.com

Colors

Designer to choose colors to be used in the design.

Requirements
Nice to have
• Nice to hace the words: Strategy, execution, results
• Nice to vave the claim: Lantern of the Steady Harvest
• The three colors should be shown:
• cyan for STRATEGY
• green for EXECUTION
• blue for RESULTS
Should not have
• Complete black background

```html
<!DOCTYPE html>
<html lang="en">
<head>
<meta charset="utf-8">
<title>BrivoTerna — Business Card</title>
<link href="https://fonts.googleapis.com/css2?family=Josefin+Sans:wght@300;400;600;700&display=swap" rel="stylesheet">
<style>
  :root {
    --bg: #e4e4e2;
    --paper: #f7f7f5;
    --navy: #24399a;
    --navy-deep: #1f3290;
    --cyan: #2aa8dc;
    --green: #8cc63f;
    --grey-text: #8a8a8a;
    --white: #ffffff;
  }
  * { box-sizing: border-box; margin: 0; padding: 0; }
  html, body { width: 1200px; height: 801px; overflow: hidden; }
  body {
    background: var(--bg);
    font-family: "Josefin Sans", sans-serif;
    display: flex;
    align-items: center;
    justify-content: center;
    gap: 40px;
  }
  .card {
    position: relative;
    width: 540px;
    height: 309px;
    border-radius: 2px;
    box-shadow: 0 6px 18px rgba(0,0,0,0.14);
    overflow: hidden;
  }

  /* Front */
  .card-front { background: var(--paper); }
  .brand {
    position: absolute;
    left: 56px; top: 40px;
    display: flex; align-items: center; gap: 12px;
  }
  .brand-dot {
    width: 26px; height: 26px; border-radius: 50%;
    background: var(--navy);
  }
  .brand-name {
    font-size: 40px; font-weight: 700; color: var(--navy);
    letter-spacing: -0.5px; line-height: 1;
  }
  .person { position: absolute; left: 96px; top: 100px; }
  .person-name { font-size: 20px; font-weight: 600; color: var(--navy); }
  .person-role { font-size: 15px; font-weight: 300; color: var(--grey-text); margin-top: 4px; }
  .accent-dashes { display: flex; gap: 6px; margin-top: 10px; }
  .accent-dashes span { width: 26px; height: 3px; }
  .dash-cyan { background: var(--cyan); }
  .dash-green { background: var(--green); }
  .dash-navy { background: var(--navy); }

  .contact {
    position: absolute; left: 56px; top: 186px;
    display: flex; flex-direction: column; gap: 6px;
    font-size: 12.5px; font-weight: 300; color: var(--grey-text);
  }
  .contact-row { display: flex; align-items: center; gap: 8px; }
  .contact-row svg { width: 14px; height: 14px; flex: none; }
  .contact-web { padding-left: 22px; }
  .contact-web strong { font-weight: 700; color: var(--navy); }

  .process-band { position: absolute; left: 0; bottom: 0; width: 540px; height: 36px; }
  .process-band text {
    font-family: "Josefin Sans", sans-serif;
    font-size: 15px; font-weight: 400; fill: var(--white); letter-spacing: 1px;
  }

  /* Back */
  .card-back {
    background: var(--navy);
    display: flex; align-items: flex-end; justify-content: center;
  }
  .back-field {
    position: absolute; inset: 0;
    background: radial-gradient(ellipse at 60% 35%, #2c44a8 0%, var(--navy) 55%, var(--navy-deep) 100%);
  }
  .tagline {
    position: relative;
    margin-bottom: 64px;
    font-size: 17px; font-weight: 400; letter-spacing: 1.6px;
    text-transform: uppercase; color: #eef1fb;
  }
</style>
</head>
<body>

  <section class="card card-front" aria-label="Business card front">
    <div class="brand">
      <span class="brand-dot"></span>
      <span class="brand-name">BrivoTerna</span>
    </div>

    <div class="person">
      <p class="person-name">Teodoro Vinsquel</p>
      <p class="person-role">CEO &amp; Founder</p>
      <div class="accent-dashes"><span class="dash-cyan"></span><span class="dash-green"></span><span class="dash-navy"></span></div>
    </div>

    <div class="contact">
      <div class="contact-row">
        <svg viewBox="0 0 14 14" aria-hidden="true"><circle cx="7" cy="7" r="7" fill="#2aa8dc"/><path d="M4.3 4.2c.3-.4.8-.4 1.1 0l.7 1c.2.3.1.6-.1.8l-.4.4c.4.9 1.1 1.6 2 2l.4-.4c.2-.2.5-.3.8-.1l1 .7c.4.3.4.8 0 1.1-.6.6-1.5.7-2.3.3C6 9.4 4.6 8 3.9 6.5c-.4-.8-.2-1.7.4-2.3z" fill="#fff"/></svg>
        <span>+34 655.803.912</span>
      </div>
      <div class="contact-row">
        <svg viewBox="0 0 14 14" aria-hidden="true"><circle cx="7" cy="7" r="7" fill="#8cc63f"/><rect x="3.5" y="4.5" width="7" height="5" fill="none" stroke="#fff" stroke-width="0.9"/><path d="M3.5 4.7 7 7.4l3.5-2.7" fill="none" stroke="#fff" stroke-width="0.9"/></svg>
        <span>teodoro.vinsquel@brivoterna-example.com</span>
      </div>
      <div class="contact-row contact-web">
        <span>www.<strong>brivoterna</strong>-example.com</span>
      </div>
    </div>

    <svg class="process-band" viewBox="0 0 540 36" aria-label="Strategy, Execution, Results">
      <polygon points="340,0 540,0 540,36 340,36" fill="#24399a"/>
      <polygon points="176,0 340,0 356,18 340,36 176,36" fill="#8cc63f"/>
      <polygon points="0,0 176,0 192,18 176,36 0,36" fill="#2aa8dc"/>
      <text x="88" y="24" text-anchor="middle">STRATEGY</text>
      <text x="266" y="24" text-anchor="middle">EXECUTION</text>
      <text x="448" y="24" text-anchor="middle">RESULTS</text>
    </svg>
  </section>

  <section class="card card-back" aria-label="Business card back">
    <div class="back-field" role="img" aria-label="Subtle embossed repeating brand-symbol texture on blue"></div>
    <p class="tagline">Lantern of the Steady Harvest</p>
  </section>

</body>
</html>
```